its a new company based in Christchurch new Zealand building computers ,repairs, upgrades and anything computers for the general public,i like bright happy colours like yellows, greens reds anything that stands out and it needs to communicant trust and security towards my new company,i have no logo yet,

Target Market(s)

target market of all ages

Industry/Entity Type

Building

Contact Information for Business Card

Byte Harbour Limited,ph-0218847261,email-tidelark77@mailvesta.test,14c marlowe cres,fenwick

```html
<!DOCTYPE html>
<html lang="en">
<head>
<meta charset="utf-8">
<title>Byte Harbour Limited – Business Card</title>
<link rel="stylesheet" href="https://fonts.googleapis.com/css2?family=Michroma&family=Open+Sans:wght@400;700&display=swap">
<style>
  :root {
    --bg: #e9e6e2;
    --card-black: #231f20;
    --card-black-deep: #161314;
    --red: #e3232a;
    --red-deep: #b5161c;
    --white: #ffffff;
    --screen-light: #6f9ee0;
    --screen-dark: #1f4f9c;
  }
  * { box-sizing: border-box; margin: 0; padding: 0; }
  html, body { width: 1200px; height: 855px; overflow: hidden; }
  body {
    background: var(--bg);
    font-family: "Open Sans", Arial, sans-serif;
    position: relative;
  }
  .card {
    position: absolute;
    left: 110px; top: 148px;
    width: 980px; height: 560px;
    border-radius: 32px;
    overflow: hidden;
    background: linear-gradient(160deg, var(--card-black) 0%, var(--card-black-deep) 100%);
    box-shadow: 0 10px 30px rgba(0,0,0,.25);
    color: var(--white);
  }
  .top-band {
    position: absolute; left: 0; top: 0;
    width: 100%; height: 26px;
    background: linear-gradient(90deg, var(--red-deep), var(--red));
  }
  .name-tab {
    position: absolute; right: 0; top: 0;
    width: 380px; height: 112px;
    background: linear-gradient(180deg, var(--red), var(--red-deep));
    border-bottom-left-radius: 26px;
    display: flex; align-items: center; justify-content: center;
    font-weight: 700; font-size: 34px; letter-spacing: .5px;
    text-transform: uppercase;
  }
  .company-name {
    position: absolute; left: 52px; top: 62px;
    font-family: "Michroma", Arial, sans-serif;
    font-size: 38px; color: var(--white);
    white-space: nowrap;
  }
  .monitor-row {
    position: absolute; left: 150px; top: 150px;
    width: 660px; height: 150px;
    display: flex; justify-content: space-between; align-items: center;
  }
  .monitor {
    width: 170px; height: 120px;
    border-radius: 6px;
    background: linear-gradient(160deg, var(--screen-light), var(--screen-dark));
    border: 6px solid #0d0d0f;
  }
  .contact-panel {
    position: absolute; left: 0; bottom: 0;
    width: 520px; height: 236px;
    background: linear-gradient(90deg, var(--red-deep), var(--red));
    border-top-right-radius: 30px;
    padding: 34px 0 0 52px;
  }
  .contact-line {
    display: flex; align-items: center;
    font-size: 30px; line-height: 1;
    margin-bottom: 22px;
    white-space: nowrap;
  }
  .contact-icon { width: 34px; height: 34px; margin-right: 18px; flex: none; }
  .services {
    position: absolute; left: 560px; top: 346px;
    width: 400px;
  }
  .services-title {
    font-family: "Michroma", Arial, sans-serif;
    font-size: 30px; margin-bottom: 12px; text-transform: uppercase;
  }
  .services-list { list-style: none; font-size: 25px; line-height: 1.3; }
</style>
</head>
<body>
  <article class="card">
    <div class="top-band"></div>
    <div class="name-tab">Your name here</div>
    <div class="company-name">Byte Harbour Limited</div>

    <div class="monitor-row">
      <div class="monitor" role="img" aria-label="Computer monitor illustration with stethoscope on screen"></div>
      <div class="monitor" role="img" aria-label="Computer monitor illustration with crossed tools on screen"></div>
      <div class="monitor" role="img" aria-label="Computer monitor illustration with blank screen"></div>
    </div>

    <section class="contact-panel">
      <div class="contact-line">
        <svg class="contact-icon" viewBox="0 0 34 34" aria-hidden="true">
          <circle cx="17" cy="17" r="16" fill="none" stroke="#fff" stroke-width="2"/>
          <rect x="11" y="8" width="12" height="18" rx="2" fill="#fff"/>
          <rect x="13" y="10" width="8" height="11" fill="#d41f26"/>
        </svg>
        0218847261
      </div>
      <div class="contact-line">
        <svg class="contact-icon" viewBox="0 0 34 34" aria-hidden="true">
          <circle cx="17" cy="17" r="16" fill="none" stroke="#fff" stroke-width="2"/>
          <rect x="8" y="11" width="18" height="12" fill="#fff"/>
          <path d="M8 11 L17 18 L26 11" fill="none" stroke="#d41f26" stroke-width="2"/>
        </svg>
        tidelark77@mailvesta.test
      </div>
      <div class="contact-line">
        <svg class="contact-icon" viewBox="0 0 34 34" aria-hidden="true">
          <circle cx="17" cy="17" r="16" fill="none" stroke="#fff" stroke-width="2"/>
          <path d="M17 27 C12 20 11 17 11 14 a6 6 0 0 1 12 0 c0 3 -1 6 -6 13z" fill="#fff"/>
          <circle cx="17" cy="14" r="2.4" fill="#d41f26"/>
        </svg>
        14c marlowe cres,fenwick
      </div>
    </section>

    <section class="services">
      <h2 class="services-title">Services</h2>
      <ul class="services-list">
        <li>Computer building</li>
        <li>Repairs, upgrades and</li>
        <li>anything computers for the general public</li>
      </ul>
    </section>
  </article>
</body>
</html>
```